Recruiting Firm Need Professional, Modern Tri-Fold Brochure for their United States Based Business

-We need a professional, modern TRI-FOLD brochure design that can help generate business for our recruiting firm. We need an impressive brochure.
- Please use the about us website content and attached website content. Website: www.morvellstaffingpartners.example
- Please use logo files attached.
- Please note: This brochure will be the starting point for an upgraded website design so we are NOT looking for a brochure to look like our current website.
- We want potential clients to want to do business with us just based on the brochure look and feel alone.

Target Market(s)

small, medium, and large companies who need administrative, human resources, and accounting talent

Industry/Entity Type

Professional Service

Font styles to use
Serif

Requirements
Must have
• - Professional, Modern TRI-FOLD Brochure Design for United States Based Company
• - Please show diverse group of professionals pictures similar to the ones on our website. One pic must include an African American female and one pic must include an African male. Or both an African American female and male can be include in the group of other races. But All the group photos must be diverse in race and include both male and female.
• - Please show pics of one business professional too
• a diverse group photo would be nice on the front cover...so we can show diversity and inclusion from the start
Should not have
• - Please DO NOT use the same pictures on our website.

```html
<!DOCTYPE html>
<html lang="en">
<head>
<meta charset="utf-8">
<title>Morvell Staffing Partners – Tri-Fold Brochure</title>
<link href="https://fonts.googleapis.com/css2?family=Open+Sans:wght@400;600&display=swap" rel="stylesheet">
<style>
  :root {
    --backdrop: #2a2a2c;
    --paper-light: #f1f1f1;
    --paper-mid: #dcdcdc;
    --brand-red: #b30d12;
    --brand-red-dark: #8c090d;
    --ink-black: #0d0d0d;
    --ink-grey: #333333;
    --white: #ffffff;
    --photo-office: #b9bcc0;
    --photo-office-dark: #6e7075;
    --photo-team: #d8d2cc;
    --photo-team-dark: #5a5c63;
  }
  * { box-sizing: border-box; margin: 0; padding: 0; }
  html, body { width: 1200px; height: 800px; overflow: hidden; }
  body {
    background: var(--backdrop);
    font-family: "Open Sans", Arial, sans-serif;
    color: var(--ink-grey);
  }
  .brochure {
    position: absolute; left: 30px; top: 30px;
    width: 1140px; height: 740px;
    background: linear-gradient(180deg, var(--paper-light), var(--paper-mid));
    overflow: hidden;
    box-shadow: 0 8px 28px rgba(0,0,0,.55);
  }
  .fold { position: absolute; top: 0; bottom: 0; width: 1px; background: rgba(0,0,0,.08); z-index: 5; }
  .fold--first { left: 380px; }
  .fold--second { left: 760px; }

  .photo { position: absolute; }
  .photo--professional {
    left: 0; top: 0; width: 380px; height: 620px;
    background: linear-gradient(160deg, var(--photo-office) 0%, #cfd1d4 45%, var(--photo-office-dark) 100%);
  }
  .photo--team {
    left: 760px; top: 160px; width: 380px; height: 300px;
    background: linear-gradient(120deg, var(--photo-team) 0%, #b7aea6 40%, var(--photo-team-dark) 100%);
  }

  .bands { position: absolute; inset: 0; width: 1140px; height: 740px; }

  .stamp-box {
    position: absolute; left: 632px; top: 48px; width: 86px; height: 96px;
    background: #e2e2e2; border: 1px solid #c9c9c9;
  }
  .posting-details {
    position: absolute; left: 380px; width: 380px; top: 290px;
    text-align: center; font-size: 20px; color: var(--ink-grey);
  }

  .brand { position: absolute; display: flex; align-items: center; gap: 10px; }
  .brand__mark { width: 30px; height: 30px; background: var(--brand-red); flex: none; }
  .brand__name {
    font-size: 19px; font-weight: 600; letter-spacing: .5px; white-space: nowrap;
  }
  .brand--cover { left: 760px; width: 380px; top: 70px; justify-content: center; }
  .brand--cover .brand__name { color: var(--ink-grey); }
  .brand--back { left: 380px; width: 380px; top: 530px; justify-content: center; }
  .brand--back .brand__mark { background: var(--white); width: 24px; height: 24px; }
  .brand--back .brand__name { color: var(--white); font-size: 17px; }

  .divider {
    position: absolute; left: 470px; width: 200px; top: 575px; height: 1px;
    background: linear-gradient(90deg, transparent, rgba(255,255,255,.8), transparent);
  }

  .contact { position: absolute; color: var(--white); list-style: none; }
  .contact li { display: flex; align-items: center; gap: 8px; white-space: nowrap; }
  .contact svg { flex: none; }
  .contact--back { left: 380px; width: 380px; top: 590px; font-size: 13px; }
  .contact--back li { justify-content: center; margin-bottom: 8px; }
  .contact--front { left: 40px; top: 640px; }
  .contact--front .contact__phone { font-size: 24px; margin-bottom: 8px; }
  .contact--front .contact__web { font-size: 13px; }

  .tagline {
    position: absolute; left: 760px; width: 380px; top: 500px;
    text-align: center; color: var(--white); font-size: 19px; line-height: 1.4;
  }
</style>
</head>
<body>
  <main class="brochure">
    <div class="photo photo--professional" role="img" aria-label="Photo of a business professional at her desk talking on the phone"></div>
    <div class="photo photo--team" role="img" aria-label="Photo of a diverse group of smiling professionals giving thumbs up"></div>

    <svg class="bands" viewBox="0 0 1140 740" aria-hidden="true">
      <path d="M0,520 C330,430 700,400 1140,345 L1140,740 L0,740 Z" fill="#ffffff"/>
      <path d="M0,540 C330,450 700,420 1140,365 L1140,740 L0,740 Z" fill="#0d0d0d"/>
      <path d="M0,600 C330,500 700,450 1140,400 L1140,740 L0,740 Z" fill="#ffffff"/>
      <path d="M0,620 C330,515 700,465 1140,415 L1140,740 L0,740 Z" fill="#b30d12"/>
      <path d="M0,740 L0,700 C400,690 800,690 1140,680 L1140,740 Z" fill="#8c090d" opacity=".35"/>
    </svg>

    <div class="fold fold--first"></div>
    <div class="fold fold--second"></div>

    <div class="stamp-box" aria-label="Postage area"></div>
    <p class="posting-details">Posting Details Here</p>

    <div class="brand brand--cover">
      <span class="brand__mark"></span>
      <span class="brand__name">Morvell Staffing Partners</span>
    </div>

    <p class="tagline">Providing<br>Top-Notch Administrative,<br>Human Resources,<br>and Accounting Talent</p>

    <div class="brand brand--back">
      <span class="brand__mark"></span>
      <span class="brand__name">Morvell Staffing Partners</span>
    </div>
    <div class="divider"></div>
    <ul class="contact contact--back">
      <li>
        <svg width="13" height="13" viewBox="0 0 24 24"><circle cx="12" cy="12" r="11" fill="none" stroke="#fff" stroke-width="2"/><path d="M8 6c1 0 2 2 2 3s-1 1-1 2 3 4 4 4 1-1 2-1 3 1 3 2-2 2-3 2c-4 0-9-5-9-9 0-1 1-3 2-3z" fill="#fff"/></svg>
        555-014-0627
      </li>
      <li>
        <svg width="14" height="11" viewBox="0 0 24 18"><rect x="1" y="1" width="22" height="16" fill="none" stroke="#fff" stroke-width="2"/><path d="M1 1l11 9 11-9" fill="none" stroke="#fff" stroke-width="2"/></svg>
        info@morvellstaffingpartners.example
      </li>
      <li>
        <svg width="13" height="13" viewBox="0 0 24 24"><circle cx="12" cy="12" r="11" fill="none" stroke="#fff" stroke-width="2"/><path d="M1 12h22M12 1c4 4 4 18 0 22M12 1c-4 4-4 18 0 22" fill="none" stroke="#fff" stroke-width="1.5"/></svg>
        www.morvellstaffingpartners.example
      </li>
    </ul>

    <ul class="contact contact--front">
      <li class="contact__phone">
        <svg width="22" height="22" viewBox="0 0 24 24"><circle cx="12" cy="12" r="11" fill="none" stroke="#fff" stroke-width="2"/><path d="M8 6c1 0 2 2 2 3s-1 1-1 2 3 4 4 4 1-1 2-1 3 1 3 2-2 2-3 2c-4 0-9-5-9-9 0-1 1-3 2-3z" fill="#fff"/></svg>
        555-014-0627
      </li>
      <li class="contact__web">
        <svg width="14" height="14" viewBox="0 0 24 24"><circle cx="12" cy="12" r="11" fill="none" stroke="#fff" stroke-width="2"/><path d="M1 12h22M12 1c4 4 4 18 0 22M12 1c-4 4-4 18 0 22" fill="none" stroke="#fff" stroke-width="1.5"/></svg>
        www.morvellstaffingpartners.example
      </li>
    </ul>
  </main>
</body>
</html>
```